Business Card Design For Office Furniture Clearance Company

Kestrel Office Clearance - our company name pretty much explains what we do, we clear offices for high end clients, mainly plc's and large international companies.

We require a nice looking business card that displays professionalism but without being too serious.

It would be nice to see just a little more than a conventional boring business card, make sure you add some flare.

Industry/Entity Type

Office Furniture

Contact Information for Business Card

CARD 1

Mark Holloway
Director
mark@kestrelofficeclearance.co.uk
m: 07700 153928

t: 01632 960418
www.kestrelofficeclearance.co.uk

Kestrel Office Clearance
Unit K4 B
2-8 Fenwick Lane
Ashbury
Stanmoor Vale
ZZ9 4QT

free office clearances… you cant get better than that.

CARD 2

Peter Radford
Director
peter@kestrelofficeclearance.co.uk
m: 07700 382615

t: 01632 960418

Kestrel Office Clearance
Unit K4 B
2-8 Fenwick Lane
Ashbury
Stanmoor Vale
ZZ9 4QT

Font styles to use
Sans Serif

Requirements
Must have
• A white background - as we have a blue logo.
Nice to have
• Nice use of the logo - play around with this and dissect it.

```html
<!DOCTYPE html>
<html lang="en">
<head>
<meta charset="utf-8">
<title>Kestrel Office Clearance – Business Card</title>
<link rel="stylesheet" href="https://fonts.googleapis.com/css2?family=Lato:wght@400;700&display=swap">
<style>
  :root {
    --page-bg: #e8e6e3;
    --card-white: #f4f3f4;
    --brand-blue: #0a7bc1;
    --brand-deep: #07609c;
    --ink-white: #ffffff;
  }
  html, body {
    margin: 0;
    padding: 0;
    width: 1138px;
    height: 1200px;
    overflow: hidden;
    background: var(--page-bg);
    font-family: "Lato", sans-serif;
  }
  .canvas { position: relative; width: 1138px; height: 1200px; }
  .card {
    position: absolute;
    border-radius: 16px;
    overflow: hidden;
    box-shadow: 0 4px 12px rgba(0,0,0,0.25);
  }
  .card--front { left: 218px; top: 198px; width: 671px; height: 384px; }
  .card--back  { left: 216px; top: 617px; width: 670px; height: 381px; }
  .card svg { display: block; width: 100%; height: 100%; }
  .card text { font-family: "Lato", sans-serif; fill: var(--ink-white); }
  .front-bg { fill: var(--card-white); }
  .wave-deep { fill: var(--brand-deep); }
  .wave-main { fill: var(--brand-blue); }
  .wave-line { fill: none; stroke: var(--ink-white); stroke-width: 3; }
  .badge-ring { fill: var(--ink-white); }
  .badge-disc { fill: var(--brand-blue); }
  .badge-name { font-weight: 700; font-size: 46px; }
  .person-name { font-weight: 700; font-size: 28px; }
  .person-role { font-size: 19px; }
  .contact-line { font-size: 18.5px; }
  .address-line { font-size: 19.5px; }
  .company-name { font-weight: 700; font-size: 34px; }
  .icon { fill: none; stroke: var(--ink-white); stroke-width: 2; }
  .icon-solid { fill: var(--ink-white); }
  .back-bg { fill: var(--brand-blue); }
  .back-name { font-weight: 700; font-size: 112px; }
  .back-web { font-size: 19px; }
</style>
</head>
<body>
<div class="canvas">

  <section class="card card--front" aria-label="Business card front">
    <svg viewBox="0 0 839 480" xmlns="http://www.w3.org/2000/svg">
      <rect class="front-bg" width="839" height="480"/>
      <path class="wave-deep" d="M0,273 C60,322 140,352 220,352 C400,350 560,82 760,78 L839,80 L839,480 L0,480 Z"/>
      <path class="wave-main" d="M0,318 C70,370 140,392 200,390 C390,382 560,96 760,86 L839,90 L839,480 L0,480 Z"/>
      <path class="wave-line" d="M0,318 C70,370 140,392 200,390 C390,382 560,96 760,86 L839,90"/>

      <circle class="badge-ring" cx="194" cy="180" r="123"/>
      <circle class="badge-disc" cx="194" cy="180" r="118"/>
      <text class="badge-name" x="194" y="196" text-anchor="middle">Kestrel</text>

      <text class="person-name" x="793" y="204" text-anchor="end">Mark Holloway</text>
      <text class="person-role" x="793" y="229" text-anchor="end">Director</text>

      <text class="contact-line" x="765" y="286" text-anchor="end">07700 153928</text>
      <rect class="icon" x="777" y="270" width="11" height="19" rx="2"/>
      <text class="contact-line" x="765" y="312" text-anchor="end">01632 960418</text>
      <path class="icon-solid" d="M778,297 l4,-1 l3,5 l-3,2 c1,3 3,5 6,6 l2,-3 l5,3 l-1,4 c-8,1 -17,-8 -16,-16 z"/>
      <text class="contact-line" x="765" y="340" text-anchor="end">mark@kestrelofficeclearance.co.uk</text>
      <rect class="icon-solid" x="776" y="327" width="17" height="12"/>
      <path d="M776,327 l8.5,7 l8.5,-7" fill="none" stroke="var(--brand-blue)" stroke-width="1.5"/>
      <text class="contact-line" x="765" y="364" text-anchor="end">www.kestrelofficeclearance.co.uk</text>
      <g class="icon" style="stroke-width:1.5">
        <circle cx="784" cy="358" r="9"/>
        <ellipse cx="784" cy="358" rx="4" ry="9"/>
        <line x1="775" y1="358" x2="793" y2="358"/>
        <line x1="777" y1="353" x2="791" y2="353"/>
        <line x1="777" y1="363" x2="791" y2="363"/>
      </g>

      <text class="address-line" x="791" y="410" text-anchor="end">Unit K4 B, 2-8 Fenwick Lane Ashbury</text>
      <text class="address-line" x="791" y="435" text-anchor="end">Stanmoor Vale ZZ9 4QT</text>

      <text class="company-name" x="56" y="433">Kestrel Office Clearance</text>
    </svg>
  </section>

  <section class="card card--back" aria-label="Business card back">
    <svg viewBox="0 0 837 477" xmlns="http://www.w3.org/2000/svg">
      <rect class="back-bg" width="837" height="477"/>
      <text class="back-name" x="418" y="282" text-anchor="middle">Kestrel</text>
      <text class="back-web" x="418" y="447" text-anchor="middle">www.kestrelofficeclearance.co.uk</text>
    </svg>
  </section>

</div>
</body>
</html>
```